RWT Fittings Ltd Business Cards

We need a business card with our business logo. We provide window and door installations on high-rises in west coast British Colombia, Canada.

I would like my business information and details on one side of the card, and the other side the company name with logo

Target Market(s)

General Contractors

Industry/Entity Type

Construction

Contact Information for Business Card

one side i want my company name and logo in the dark theme logo that i provided

Requirements
Must have
• Marco Peltieri, 16045518293, RWTFittings@mailbox-demo.com, 1407-5194 Linden Row Burnaby BC, V5H 2K9, Owner & Manager

```html
<!DOCTYPE html>
<html lang="en">
<head>
<meta charset="utf-8">
<title>RWT Fittings Ltd – Business Cards</title>
<link rel="stylesheet" href="https://fonts.googleapis.com/css2?family=Montserrat:wght@400;500;700&display=swap">
<style>
  :root {
    --backdrop: #d9d9d9;
    --card-dark-1: #3b3a3b;
    --card-dark-2: #211e1f;
    --brand-blue: #2aa6de;
    --blue-light: #5db9e0;
    --blue-deep: #1f97cb;
    --mark-grey: #a6a6a6;
    --panel-light: #ececec;
    --panel-grey: #8a8a8a;
    --white: #ffffff;
  }
  * { box-sizing: border-box; margin: 0; padding: 0; }
  html, body { width: 1200px; height: 1200px; overflow: hidden; }
  body {
    background: var(--backdrop);
    font-family: "Montserrat", sans-serif;
    position: relative;
  }
  .card {
    position: absolute;
    left: 180px;
    width: 840px;
    height: 480px;
    border-radius: 30px;
    overflow: hidden;
  }
  .card--front {
    top: 90px;
    background: linear-gradient(120deg, var(--card-dark-1) 0%, var(--card-dark-2) 55%);
    display: flex;
    align-items: center;
    justify-content: center;
    gap: 26px;
  }
  .brand-square {
    width: 40px;
    height: 40px;
    background: var(--mark-grey);
  }
  .brand-name {
    color: var(--brand-blue);
    font-weight: 700;
    font-size: 60px;
    letter-spacing: 2px;
  }
  .card--back {
    top: 630px;
    background: linear-gradient(100deg, var(--blue-light) 0%, var(--blue-deep) 60%);
    color: var(--white);
  }
  .decoration {
    position: absolute;
    right: 0;
    top: 0;
    width: 400px;
    height: 480px;
  }
  .identity {
    position: absolute;
    left: 52px;
    top: 62px;
  }
  .identity__name { font-weight: 700; font-size: 38px; letter-spacing: 0.5px; }
  .identity__title { font-weight: 400; font-size: 20px; margin-top: 6px; letter-spacing: 0.5px; }
  .contact {
    position: absolute;
    left: 52px;
    top: 250px;
    font-size: 19px;
    line-height: 1.45;
    letter-spacing: 0.3px;
  }
  .contact__address { margin-bottom: 14px; }
  .contact__line { display: flex; align-items: center; gap: 12px; }
  .contact__icon { width: 18px; height: 18px; flex: none; }
</style>
</head>
<body>
  <section class="card card--front" aria-label="Card front">
    <span class="brand-square"></span>
    <span class="brand-name">RWT Fittings Ltd</span>
  </section>

  <section class="card card--back" aria-label="Card back">
    <svg class="decoration" viewBox="0 0 400 480" role="img" aria-label="Large building mark decoration in grey and white">
      <defs>
        <linearGradient id="decoFill" x1="0" y1="0" x2="1" y2="1">
          <stop offset="0" stop-color="#ececec"/>
          <stop offset="1" stop-color="#9a9a9a"/>
        </linearGradient>
      </defs>
      <polygon points="40,150 400,90 400,480 120,480" fill="url(#decoFill)"/>
    </svg>

    <div class="identity">
      <h1 class="identity__name">Marco Peltieri</h1>
      <p class="identity__title">Owner &amp; Manager</p>
    </div>

    <div class="contact">
      <p class="contact__address">1407-5194 Linden Row<br>Burnaby BC, V5H 2K9</p>
      <p class="contact__line">
        <svg class="contact__icon" viewBox="0 0 24 24" aria-hidden="true"><path fill="#fff" d="M6.6 10.8a15.2 15.2 0 0 0 6.6 6.6l2.2-2.2a1 1 0 0 1 1-.25 11.4 11.4 0 0 0 3.6.57 1 1 0 0 1 1 1V20a1 1 0 0 1-1 1A17 17 0 0 1 3 4a1 1 0 0 1 1-1h3.5a1 1 0 0 1 1 1c0 1.250.2 2.45.57 3.57a1 1 0 0 1-.25 1z"/></svg>
        16045518293
      </p>
      <p class="contact__line">
        <svg class="contact__icon" viewBox="0 0 24 24" aria-hidden="true"><path fill="#fff" d="M2 5h20v14H2z"/><path fill="none" stroke="#2aa6de" stroke-width="2" d="M2 5l10 8 10-8"/></svg>
        RWTFittings@mailbox-demo.com
      </p>
      <p class="contact__line">
        <svg class="contact__icon" viewBox="0 0 24 24" aria-hidden="true"><circle cx="12" cy="12" r="10" fill="#fff"/><path fill="none" stroke="#2aa6de" stroke-width="1.6" d="M2 12h20M12 2c3 3 3 17 0 20M12 2c-3 3-3 17 0 20"/></svg>
        www.rwtfittings-demo.com
      </p>
    </div>
  </section>
</body>
</html>
```